Layout für Broschüre für chemiefreie Lösung, Kühlwasser aufzubereiten
Zielgruppe
FLUVITEK hat eine Technologie entwickelt, die in der Industrie eingesetzt wird um in geschlossenen und offenen Kühlkreisläufen ohne Biozide und Korrosion Inhibitoren das Kühlwasser aufzubereiten. Mit FLUVITEK haben die Unternehmen eine chemiefreie Lösungen gegen Biofouling, Korrosion und Kalk. Zielgruppe sind alle Unternehmen die etwas produzieren oder Klimaanlagen / Heizungssysteme betreiben. Es geht um zukunftsorientierte und vor allem nachhaltige Technologie ohne Einsatz von Chemie.
Aufgabenstellung
Wir suchen für die Broschüre ein neues Layout, dass geradlinig und klar strukturiert ist, vor allem modern. Die Broschüre sollte DIN A 4 - Format sein in der gewohnten Struktur Umschlagseite innen und außen und 8 - 10 Innenseiten. Im Layout sollte ein roter Faden zu erkennen sein, aber nicht jede Seite gleich aussehen. Die Anlagen sind nur beispielhaft vom bestehenden Material und sollten vom Layout keinesfalls eine Orientierung geben, denn das soll verändert werden. Die Anlagen sind für einen inhaltlichen Überblick.

```html
<!DOCTYPE html>
<html lang="de">
<head>
<meta charset="utf-8">
<title>FLUVITEK – Broschüre Umschlag</title>
<link href="https://fonts.googleapis.com/css2?family=Inter:wght@200;300;400;600&display=swap" rel="stylesheet">
<style>
  :root {
    --bg: #d2d2d2;
    --navy-deep: #05052c;
    --navy-band: #4a5276;
    --spine: #3a3aa8;
    --photo-dark: #2a2a2c;
    --photo-mid: #6b6b6e;
    --photo-light: #a9a9ab;
    --white: #ffffff;
    --text-soft: #c9cde0;
    --text-muted: #5a5f9a;
    --brand: #7dbb45;
  }
  * { margin: 0; padding: 0; box-sizing: border-box; }
  html, body { width: 1200px; height: 900px; overflow: hidden; }
  body {
    background: var(--bg);
    font-family: "Inter", Arial, sans-serif;
    display: flex;
    align-items: center;
    justify-content: center;
  }
  .cover-spread {
    display: flex;
    box-shadow: 0 12px 30px rgba(0,0,0,0.18);
  }
  .page {
    width: 420px;
    height: 594px;
    position: relative;
    overflow: hidden;
  }
  .spine {
    width: 8px;
    height: 594px;
    background: var(--spine);
  }

  /* Back cover */
  .back-cover { background: var(--navy-deep); }
  .back-cover__info {
    position: absolute;
    left: 46px;
    bottom: 58px;
    width: 200px;
  }
  .back-cover__headline {
    font-size: 8px;
    font-weight: 400;
    color: var(--text-muted);
    margin-bottom: 4px;
  }
  .back-cover__body {
    font-size: 5.5px;
    line-height: 1.5;
    color: var(--text-muted);
    margin-bottom: 10px;
  }

  /* Brand lockup */
  .brand {
    display: flex;
    align-items: center;
    gap: 5px;
    font-weight: 600;
    font-size: 11px;
    letter-spacing: 0.04em;
    color: var(--brand);
  }
  .brand__dot {
    width: 8px; height: 8px;
    border-radius: 50%;
    background: var(--brand);
  }

  /* Front cover */
  .front-cover { background: var(--navy-band); }
  .front-cover__photo {
    position: absolute;
    left: 0; top: 0;
    width: 100%;
    height: 370px;
    background:
      radial-gradient(ellipse at 45% 30%, var(--photo-light) 0%, var(--photo-mid) 35%, transparent 70%),
      linear-gradient(180deg, var(--photo-mid) 0%, var(--photo-dark) 100%);
  }
  .front-cover__title {
    position: absolute;
    left: 40px;
    top: 258px;
    color: var(--white);
    font-weight: 200;
    font-size: 27px;
    line-height: 1.08;
    letter-spacing: 0.01em;
    text-transform: uppercase;
  }
  .front-cover__swoosh {
    position: absolute;
    left: 40px;
    top: 328px;
  }
  .front-cover__subtitle {
    position: absolute;
    left: 40px;
    top: 420px;
    color: var(--text-soft);
    font-size: 9px;
    font-weight: 400;
    letter-spacing: 0.14em;
    text-transform: uppercase;
  }
  .front-cover .brand {
    position: absolute;
    right: 42px;
    bottom: 96px;
  }
</style>
</head>
<body>
  <main class="cover-spread">
    <section class="page back-cover">
      <div class="back-cover__info">
        <p class="back-cover__headline">Sauberes Kühlwasser ohne Chemie für Ihre Anlagen</p>
        <p class="back-cover__body">
          Nachhaltige Technologie gegen Biofouling, Korrosion und Kalk<br>
          für offene und geschlossene Kühlkreisläufe in der Industrie<br>
          Fordern Sie jetzt Ihre persönliche Beratung an
        </p>
        <div class="brand"><span class="brand__dot"></span>FLUVITEK</div>
      </div>
    </section>

    <div class="spine"></div>

    <section class="page front-cover">
      <div class="front-cover__photo" role="img" aria-label="Schwarzweißfoto: Hand unter einem Wasserstrahl mit spritzenden Tropfen"></div>
      <h1 class="front-cover__title">Chemiefreie<br>Wasserbehandlung</h1>
      <svg class="front-cover__swoosh" width="150" height="16" viewBox="0 0 150 16" aria-hidden="true">
        <path d="M2 14 Q 70 12 148 2" fill="none" stroke="#ffffff" stroke-width="2" stroke-linecap="round"/>
      </svg>
      <p class="front-cover__subtitle">Lorem ipsum dolores</p>
      <div class="brand"><span class="brand__dot"></span>FLUVITEK</div>
    </section>
  </main>
</body>
</html>
```